New Pharmaceutical Brochure Design Project

KLW Frost Carriers provides a level of service that is more than just simply transporting your pharmaceutical and healthcare products to its final destination. We fulfil your requirements by listening to your needs and provide a transport solution that totally fits your requirements.

Our mission is to provide an incomparable service for our customers that goes beyond their expectations. Our commitment to exceptional service is to demonstrate GDP, ensuring that your healthcare products are delivered with safety and arrive at their destination intact.

We invest in the highest quality temperature controlled transport equipment available, built to unique specifications, incorporating state of the art refrigeration systems, supported by audible and visual alarms and independent back up refrigeration systems. Satellite-linked position and temperature tracking technology provide our clients with a complete real-time audit trail from the point of collection to the delivery destination.

KLW Frost Carriers are continuously updating equipment and facilities, and together with a skilled and experienced workforce will continue to exceed your expectations.

KLW Frost Carriers is a specialist courier for clinical trials, transport of clinical and medical research and logistics management. It is the number one choice for Clinical Trial Project Managers, logistics consultants, and healthcare professionals, offering them solutions for time critical and temperature sensitive shipments for pre-clinical trials and phase I – IV clinical trial material.

With a thorough knowledge of clinical trial logistics, transportation regulations, compliance and documentation, as well as protocol support and packaging, KLW is uniquely qualified to meet your specific shipping needs.

We are always on call, ready to answer questions and guide you through various logistics challenges. Our logistics specialists have a unique understanding of your needs and can provide advice and solutions in-line with your project objectives.

Target Market(s)

Pharmaceutical and medical industry

Contact Information for Business Card

Matthias Perel, Managing Director, www.klw-frostcarriers-example.com, info@klw-frostcarriers-example.com
+44 (0) 700 1594086
+44 (0) 300 912 6041

Font styles to use
Serif
Sans Serif

Requirements
Must have
• modern vibrant images and colours in shades of blue
• all wording can be taken from our websites pharmaceutical and medical pages

```html
<!DOCTYPE html>
<html lang="en">
<head>
<meta charset="utf-8">
<title>KLW Frost Carriers – Brochure Spread</title>
<link rel="stylesheet" href="https://fonts.googleapis.com/css2?family=Montserrat:ital,wght@0,300;0,400;0,500;0,600;0,700;0,800;1,400;1,600;1,700&display=swap">
<style>
  :root{
    --stage:#ececec;
    --navy:#172a6e;
    --navy-deep:#13225c;
    --band:#3c5a9c;
    --bright-blue:#2f86e8;
    --sky:#4aa8ff;
    --caption:#1f47a6;
    --paper:#ffffff;
    --paper-grey:#eff0f2;
    --ink:#2b2f3a;
    --ink-soft:#6b6f78;
    --tile-sky:#6fd0f7;
    --tile-grey:#e4e4e4;
    --tile-yellow:#fff35a;
    --icon:#5b5e66;
  }
  *{box-sizing:border-box;margin:0;padding:0}
  html,body{width:1200px;height:900px;overflow:hidden}
  body{background:var(--stage);font-family:"Montserrat",Arial,sans-serif;color:var(--ink);position:relative}

  .spread{position:absolute;left:80px;top:82px;width:1040px;height:736px;display:flex;box-shadow:0 14px 40px rgba(0,0,0,.14)}
  .page{position:relative;width:520px;height:736px;overflow:hidden}
  .page--left{background:var(--paper-grey)}
  .page--right{background:var(--paper)}
  .spine{position:absolute;left:519px;top:0;width:2px;height:736px;background:linear-gradient(90deg,rgba(0,0,0,.08),rgba(0,0,0,0))}

  /* left page */
  .intro{position:absolute;left:0;top:0;width:520px;height:340px;background:linear-gradient(160deg,var(--navy),var(--navy-deep));color:#fff;padding:38px 40px 0 44px}
  .intro__title{border-left:2px solid var(--sky);padding-left:12px;margin-bottom:18px}
  .intro__kicker{font-weight:300;font-size:15px;letter-spacing:.5px;text-transform:uppercase}
  .intro__headline{font-weight:800;font-size:22px;letter-spacing:.8px;text-transform:uppercase;line-height:1.2}
  .intro p{font-size:8.6px;line-height:1.6;font-weight:300;color:#dfe4f5;margin-bottom:7px}

  .services{position:absolute;left:40px;top:372px;width:450px}
  .services__heading{font-weight:800;font-size:17px;line-height:1.25;text-transform:uppercase;letter-spacing:.4px;color:var(--ink)}
  .services__heading em{font-style:normal;color:var(--bright-blue)}
  .service-row{display:flex;gap:12px;margin-top:20px}
  .service{width:104px;position:relative;height:130px}
  .service__photo{width:104px;height:82px;display:block}
  .service__label{position:absolute;left:-8px;top:70px;width:100px;height:52px;background:var(--caption);color:#fff;font-size:9px;font-weight:500;line-height:1.3;display:flex;align-items:center;justify-content:center;text-align:center;padding:0 8px}

  .testimonial{position:absolute;width:440px}
  .testimonial__mark{font-family:Georgia,"Times New Roman",serif;font-size:54px;line-height:1;color:#cfd2d8;font-weight:700}
  .testimonial__text{font-size:12px;line-height:1.6;color:var(--ink-soft);margin-top:-18px;padding-left:4px}
  .testimonial__by{font-size:11px;font-weight:700;color:var(--navy);margin-top:14px;text-align:center}
  .testimonial__close{text-align:right;margin-top:-10px}
  .testimonial--left{left:40px;top:590px}
  .testimonial--right{left:40px;top:588px}

  /* right page */
  .benefits{position:absolute;left:0;top:0;width:520px;height:240px;background:var(--band);color:#fff;padding:42px 44px 0}
  .benefits__heading{font-size:16px;font-weight:700;letter-spacing:.5px;text-transform:uppercase}
  .benefits__heading em{font-style:normal;color:var(--sky)}
  .benefits__text{font-size:9px;font-style:italic;line-height:1.55;margin-top:10px;width:420px;color:#eef2fb}

  .tiles{position:absolute;left:44px;top:150px;display:flex}
  .tile{width:144px;height:132px;padding:16px 14px 0;position:relative}
  .tile--sky{background:var(--tile-sky)}
  .tile--grey{background:var(--tile-grey)}
  .tile--yellow{background:var(--tile-yellow)}
  .tile__icon{display:block;margin:0 auto 10px}
  .tile__small{font-size:9px;font-weight:700;font-style:italic;text-transform:uppercase;color:var(--ink)}
  .tile__big{font-size:23px;font-weight:800;text-transform:uppercase;color:var(--ink);line-height:1.05;letter-spacing:.3px}

  .tracked{position:absolute;left:40px;top:314px}
  .tracked__kicker{font-size:15px;font-weight:700;font-style:italic;color:var(--bright-blue);text-transform:uppercase}
  .tracked__headline{font-size:13.5px;font-weight:700;text-transform:uppercase;color:var(--ink);letter-spacing:.3px;margin-top:2px}
  .tracked__screen{position:absolute;left:40px;top:376px;width:230px;height:160px;border-radius:6px;background:radial-gradient(ellipse at 50% 45%,#3a4250,#20252e 70%);box-shadow:0 6px 16px rgba(0,0,0,.15)}
  .features{position:absolute;left:292px;top:392px;width:200px}
  .features__title{font-size:9.5px;font-weight:700;color:var(--caption);margin-bottom:6px}
  .features ul{list-style:none}
  .features li{font-size:8.6px;color:var(--ink-soft);line-height:1.7;display:flex;gap:5px;align-items:center}
  .features__note{font-size:8.4px;font-style:italic;color:var(--ink-soft);line-height:1.5;margin-top:8px}
</style>
</head>
<body>
<main class="spread">
  <section class="page page--left">
    <div class="intro">
      <div class="intro__title">
        <p class="intro__kicker">A service you can trust,</p>
        <h1 class="intro__headline">People you can count on</h1>
      </div>
      <p>KLW Frost Carriers provides a level of service that is more than just simply transporting your pharmaceutical and healthcare products to its final destination. We fulfil your requirements by listening to your needs and provide a transport solution that totally fits your requirements.</p>
      <p>Our mission is to provide an incomparable service for our customers that goes beyond their expectations. Our commitment to exceptional service is to demonstrate GDP, ensuring that your healthcare products are delivered with safety and arrive at their destination intact.</p>
      <p>We invest in the highest quality temperature controlled transport equipment available, built to unique specifications, incorporating state of the art refrigeration systems, supported by audible and visual alarms and independent back up refrigeration systems. Satellite-linked position and temperature tracking technology provide our clients with a complete real-time audit trail from the point of collection to the delivery destination.</p>
      <p>KLW Frost Carriers are continuously updating equipment and facilities, and together with a skilled and experienced workforce will continue to exceed your expectations.</p>
    </div>

    <div class="services">
      <h2 class="services__heading">For all your temperature controlled<br>transport <em>needs chose KLW</em></h2>
      <div class="service-row">
        <div class="service">
          <svg class="service__photo" role="img" aria-label="Photo of a refrigerated van driving on a motorway"><defs><linearGradient id="ph1" x1="0" y1="0" x2="1" y2="1"><stop offset="0" stop-color="#8ea0b0"/><stop offset="1" stop-color="#3f5a3a"/></linearGradient></defs><rect width="104" height="82" fill="url(#ph1)"/></svg>
          <div class="service__label">UK and European deliveries</div>
        </div>
        <div class="service">
          <svg class="service__photo" role="img" aria-label="Photo of the chilled cargo area inside a van"><defs><linearGradient id="ph2" x1="0" y1="0" x2="1" y2="1"><stop offset="0" stop-color="#c9d6e4"/><stop offset="1" stop-color="#4a5a70"/></linearGradient></defs><rect width="104" height="82" fill="url(#ph2)"/></svg>
          <div class="service__label">24 monitoring and track-ing</div>
        </div>
        <div class="service">
          <svg class="service__photo" role="img" aria-label="Photo of a white refrigerated truck on the road"><defs><linearGradient id="ph3" x1="0" y1="0" x2="1" y2="1"><stop offset="0" stop-color="#2e3a2c"/><stop offset="1" stop-color="#b8bcc0"/></linearGradient></defs><rect width="104" height="82" fill="url(#ph3)"/></svg>
          <div class="service__label">Dedicated vehicles</div>
        </div>
        <div class="service">
          <svg class="service__photo" role="img" aria-label="Photo of a refrigeration unit for pharmaceutical transport"><defs><linearGradient id="ph4" x1="0" y1="0" x2="1" y2="1"><stop offset="0" stop-color="#f2f3f5"/><stop offset="1" stop-color="#c4c8ce"/></linearGradient></defs><rect width="104" height="82" fill="url(#ph4)"/></svg>
          <div class="service__label">Pharmaceutical and food industry</div>
        </div>
      </div>
    </div>

    <blockquote class="testimonial testimonial--left">
      <div class="testimonial__mark">&ldquo;</div>
      <p class="testimonial__text">Tomas and his team at Frost Carriers have a can do attitude and never let us down. Would not hesitate to recommend them.</p>
      <p class="testimonial__by">- R. D. - Food Logistics Company</p>
      <div class="testimonial__mark testimonial__close">&rdquo;</div>
    </blockquote>
  </section>

  <section class="page page--right">
    <div class="benefits">
      <h2 class="benefits__heading">Benefits of <em>working with KLW</em></h2>
      <p class="benefits__text">Fully maintained modern fleet of refrigerated vehicles. All vehicles fitted with temperature recorders. Fully tracked and available 24/7. All drivers are trained, and security checked. Flexible payment terms to suit your business. Friendly and professional staff.</p>
    </div>

    <div class="tiles">
      <div class="tile tile--sky">
        <svg class="tile__icon" width="34" height="34" viewBox="0 0 34 34" aria-hidden="true"><circle cx="17" cy="17" r="16" fill="var(--icon)"/><path d="M17 8l2.4 5 5.4.6-4 3.7 1.1 5.3L17 20l-4.9 2.6 1.1-5.3-4-3.7 5.4-.6z" fill="none" stroke="#fff" stroke-width="1.3"/></svg>
        <p class="tile__small">First class</p>
        <p class="tile__big">Service</p>
      </div>
      <div class="tile tile--grey">
        <svg class="tile__icon" width="34" height="34" viewBox="0 0 34 34" aria-hidden="true"><circle cx="17" cy="17" r="16" fill="var(--icon)"/><path d="M17 8l7 3v5c0 4.5-3 7.5-7 9-4-1.5-7-4.5-7-9v-5z" fill="none" stroke="#fff" stroke-width="1.3"/><path d="M13.5 16.5l2.5 2.5 4.5-4.5" fill="none" stroke="#fff" stroke-width="1.3"/></svg>
        <p class="tile__small">Fully</p>
        <p class="tile__big">Insured</p>
      </div>
      <div class="tile tile--yellow">
        <svg class="tile__icon" width="34" height="34" viewBox="0 0 34 34" aria-hidden="true"><circle cx="17" cy="17" r="16" fill="var(--icon)"/><circle cx="17" cy="17" r="8" fill="none" stroke="var(--tile-yellow)" stroke-width="1.5"/><path d="M17 12v5l3.5 2" fill="none" stroke="var(--tile-yellow)" stroke-width="1.5"/></svg>
        <p class="tile__small">Timely</p>
        <p class="tile__big">Delivery</p>
      </div>
    </div>

    <div class="tracked">
      <p class="tracked__kicker">Fully tracked</p>
      <h2 class="tracked__headline">Your shipment is safe, secured &amp; trackable</h2>
    </div>
    <div class="tracked__screen" role="img" aria-label="Illustration of a laptop showing a tracking map with delivery route pins"></div>

    <div class="features">
      <p class="features__title">GPS tracked vehicles</p>
      <ul>
        <li><svg width="8" height="8" viewBox="0 0 8 8" aria-hidden="true"><path d="M1 4.2l2 2L7 1.5" fill="none" stroke="var(--caption)" stroke-width="1.3"/></svg>Modern Fleet of Refrigerated Vans and Trucks</li>
        <li><svg width="8" height="8" viewBox="0 0 8 8" aria-hidden="true"><path d="M1 4.2l2 2L7 1.5" fill="none" stroke="var(--caption)" stroke-width="1.3"/></svg>Always know your delivery time</li>
        <li><svg width="8" height="8" viewBox="0 0 8 8" aria-hidden="true"><path d="M1 4.2l2 2L7 1.5" fill="none" stroke="var(--caption)" stroke-width="1.3"/></svg>All vehicles fitted with temperature recorders</li>
        <li><svg width="8" height="8" viewBox="0 0 8 8" aria-hidden="true"><path d="M1 4.2l2 2L7 1.5" fill="none" stroke="var(--caption)" stroke-width="1.3"/></svg>Live Updates</li>
        <li><svg width="8" height="8" viewBox="0 0 8 8" aria-hidden="true"><path d="M1 4.2l2 2L7 1.5" fill="none" stroke="var(--caption)" stroke-width="1.3"/></svg>Calibration Certificates</li>
        <li><svg width="8" height="8" viewBox="0 0 8 8" aria-hidden="true"><path d="M1 4.2l2 2L7 1.5" fill="none" stroke="var(--caption)" stroke-width="1.3"/></svg>Overnight Stand By and Plug Ins</li>
      </ul>
      <p class="features__note">All our vehicles are fitted with trackers so our clients can receive up to date information on the whereabouts of goods and ETAs.</p>
    </div>

    <blockquote class="testimonial testimonial--right">
      <div class="testimonial__mark">&ldquo;</div>
      <p class="testimonial__text">KLW Frost Carriers regularly deliver to one of our clients from Surrey to Manchester, they are highly professional and always on time. Can highly recommend them.</p>
      <p class="testimonial__by">L. M. - Managing Director, Pharma Company</p>
      <div class="testimonial__mark testimonial__close">&rdquo;</div>
    </blockquote>
  </section>
  <div class="spine"></div>
</main>
</body>
</html>
```